KRL Stationery Design Project

Dear Designers,
We need a new stationery design for company to match our new logo.
Designers should provide a design for the following:
1. Business Card: 3.5x2 Inches.
2. Letterhead: A4 size.
3. Envelops: 25x35.5 Cm.
You can keep the Arabic name at the bottom of the logo Or you can use the separate attached Arabic Name.
Please refer to the attached logo guide for design information.
Sample Business Card information:
Name: Tarek Sowan
Position: Operation Manager
Tel: +966 920007164 Ex. 500
Fax: +966 (3)8842617
Mob: +966 (5)00263817
email: tarek@krl-example.com.sa
URL: www.krl-example.com.sa
Address:
Nakheel Heights, Suite 718
Zayed bin Omar Str.
Khobar, 31847
Saudi Arabia
Updates
Dear All,
Please note, we had uploaded our logo along with Arabic writing in Adobe illustrator format (.ai).
Regards,
Karim
Dear All,
A sample data for the business card had been added as per your request.
Regards,
Karim

```html
<!DOCTYPE html>
<html lang="en">
<head>
<meta charset="utf-8">
<title>KRL Business Card</title>
<link rel="stylesheet" href="https://fonts.googleapis.com/css2?family=Open+Sans:wght@400;600;700&display=swap">
<style>
  :root {
    --backdrop: #2b2b2b;
    --card-light: #ffffff;
    --card-navy: #0f2c52;
    --ink-navy: #0f2c52;
    --ink-body: #333333;
    --ink-white: #ffffff;
  }
  * { margin: 0; padding: 0; box-sizing: border-box; }
  html, body {
    width: 1200px; height: 472px; overflow: hidden;
    background: var(--backdrop);
    font-family: "Open Sans", Arial, sans-serif;
  }
  .stage { position: relative; width: 1200px; height: 472px; }
  .card {
    position: absolute; top: 87px; width: 525px; height: 300px;
    border-radius: 22px; box-shadow: 0 3px 8px rgba(0,0,0,.45);
  }
  .card--front { left: 52px; background: var(--card-light); color: var(--ink-body); }
  .card--back { left: 594px; background: var(--card-navy); color: var(--ink-white); }

  .brand { position: absolute; display: flex; align-items: center; gap: 12px; font-weight: 700; }
  .brand__mark { width: 18px; height: 18px; }
  .card--front .brand { left: 24px; top: 48px; color: var(--ink-navy); font-size: 72px; line-height: 1; }
  .card--front .brand__mark { background: var(--ink-navy); }
  .card--back .brand { left: 0; right: 0; top: 100px; justify-content: center; color: var(--ink-white); font-size: 60px; line-height: 1; }
  .card--back .brand__mark { background: var(--ink-white); }

  .contact-list { position: absolute; left: 24px; top: 181px; list-style: none; font-size: 13px; line-height: 17.5px; }
  .contact-list li { display: flex; align-items: center; gap: 7px; }
  .contact-list svg { width: 11px; height: 11px; fill: var(--ink-navy); flex: none; }

  .person { position: absolute; left: 330px; width: 185px; top: 181px; text-align: center; }
  .person__name { font-size: 16px; font-weight: 700; color: var(--ink-navy); line-height: 20px; }
  .person__title { font-size: 13px; line-height: 18px; }

  .address { position: absolute; left: 24px; top: 262px; font-size: 13px; }

  .website { position: absolute; left: 0; right: 0; top: 229px; text-align: center; font-size: 12px; letter-spacing: 2px; }
</style>
</head>
<body>
<div class="stage">
  <section class="card card--front">
    <div class="brand"><span class="brand__mark"></span>KRL</div>

    <ul class="contact-list">
      <li><svg viewBox="0 0 12 12"><path d="M2.5 1l2 2.3-1 1.3a7 7 0 0 0 3.9 3.9l1.3-1 2.3 2-1.2 1.6C5.5 10.8 1.2 6.5 1 1.9z"/></svg>123-456-7890</li>
      <li><svg viewBox="0 0 12 12"><path d="M2.5 2h7l1.5 4v3.5h-1.5v1.5h-1.5v-1.5h-4v1.5h-1.5v-1.5h-1.5v-3.5z"/><rect x="3" y="3" width="6" height="2.5" fill="#fff"/></svg>123-456-7890</li>
      <li><svg viewBox="0 0 12 12"><rect x="0.5" y="2.5" width="11" height="7.5" rx="1"/><path d="M1 3l5 3.8L11 3" stroke="#fff" stroke-width="1.1" fill="none"/></svg>info@krl-example.com</li>
      <li><svg viewBox="0 0 12 12"><circle cx="6" cy="6" r="5.5"/><path d="M0.5 6h11M6 0.5c-3 3-3 8 0 11M6 0.5c3 3 3 8 0 11" stroke="#fff" stroke-width=".8" fill="none"/></svg>www.krl-example.com</li>
    </ul>

    <div class="person">
      <p class="person__name">Your name</p>
      <p class="person__title">Title</p>
    </div>

    <p class="address">Street Name, City Name, State, City Zip Code</p>
  </section>

  <section class="card card--back">
    <div class="brand"><span class="brand__mark"></span>KRL</div>
    <p class="website">www.krl-example.com</p>
  </section>
</div>
</body>
</html>
```